Brightwave Reach - Business Card

We need a business card for a Social Media Marketing company that specializes in online marketing for small businesses in Canada using common Social Media platforms such as Pixlora, Chatterly, Blinkpost & Quibber.

I have uploaded a copy of our logo which I would like utilized in the business card. We would like the business card to be modern yet classy design.

Our website is www.brightwavereach.ca

Industry/Entity Type

Marketing

Contact Information for Business Card

Email: info@brightwavereach.ca
Website: www.brightwavereach.ca
Telephone: 604-555-0193

Colors

Designer to choose colors to be used in the design.

Requirements
Must have
• Social Media icons on reverse
• Please add some designs with color.

```html
<!DOCTYPE html>
<html lang="en">
<head>
<meta charset="utf-8">
<title>Brightwave Reach – Business Card</title>
<link href="https://fonts.googleapis.com/css2?family=Source+Sans+3:wght@400;600;700&display=swap" rel="stylesheet">
<style>
  :root {
    --backdrop: #000000;
    --card: #404547;
    --ink: #ffffff;
    --ink-soft: #e4e6e7;
  }
  * { margin: 0; padding: 0; box-sizing: border-box; }
  html, body {
    width: 1200px; height: 900px; overflow: hidden;
    background: var(--backdrop);
    font-family: "Source Sans 3", Arial, sans-serif;
  }
  .stage { position: relative; width: 1200px; height: 900px; }
  .card {
    position: absolute;
    background: var(--card);
    color: var(--ink);
  }
  .card--front {
    left: 120px; top: 275px; width: 477px; height: 293px;
    border-radius: 0 46px 0 52px;
  }
  .card--back {
    left: 607px; top: 273px; width: 476px; height: 293px;
    border-radius: 46px 0 52px 0;
  }
  .brand {
    position: absolute;
    display: flex; align-items: center; gap: 10px;
    font-weight: 700; text-transform: uppercase;
    color: var(--ink); line-height: 1.0; letter-spacing: 0.5px;
  }
  .brand__mark {
    width: 14px; height: 14px; border: 2px solid var(--ink); flex: none;
  }
  .card--front .brand { left: 34px; top: 78px; font-size: 25px; }
  .card--back .brand { left: 140px; top: 114px; font-size: 30px; }
  .holder {
    position: absolute; right: 32px; top: 141px; text-align: right;
  }
  .holder__name { font-size: 15.5px; font-weight: 600; }
  .holder__role { font-size: 13px; color: var(--ink-soft); margin-top: 1px; }
  .contacts {
    position: absolute; right: 31px; top: 212px;
    list-style: none; text-align: right;
    font-size: 12.5px; line-height: 17.5px; color: var(--ink-soft);
  }
  .contacts li { display: flex; justify-content: flex-end; align-items: center; gap: 5px; }
  .contacts svg { width: 9px; height: 9px; fill: var(--ink-soft); }
</style>
</head>
<body>
<main class="stage">
  <section class="card card--front" aria-label="Card front">
    <div class="brand"><span class="brand__mark"></span><span>Brightwave<br>Reach</span></div>
    <div class="holder">
      <p class="holder__name">Daniel Morrow</p>
      <p class="holder__role">Managing Director</p>
    </div>
    <ul class="contacts">
      <li>604-555-0193
        <svg viewBox="0 0 10 10" aria-hidden="true"><path d="M1 3.5 Q5 0 9 3.5 L8 5 L6.5 4 V3.3 Q5 2.8 3.5 3.3 V4 L2 5 Z M2.5 5.5 H7.5 L8 9 H2 Z"/></svg>
      </li>
      <li>info@brightwavereach.ca
        <svg viewBox="0 0 10 10" aria-hidden="true"><path d="M1 2.5 H9 V8 H1 Z M1.5 3 L5 5.8 L8.5 3" stroke="#404547" stroke-width="0.8"/></svg>
      </li>
      <li>www.brightwavereach.ca
        <svg viewBox="0 0 10 10" aria-hidden="true"><circle cx="5" cy="5" r="4.5"/><path d="M5 0.5 V9.5 M0.5 5 H9.5" stroke="#404547" stroke-width="0.8"/></svg>
      </li>
    </ul>
  </section>

  <section class="card card--back" aria-label="Card back">
    <div class="brand"><span class="brand__mark"></span><span>Brightwave<br>Reach</span></div>
  </section>
</main>
</body>
</html>
```